Book cover for book about Climate Change

Looking for a clean, bold, and attractive cover for a mass-market paperback (5.5"x 8.5") about solving the climate change problem. Title is either "Where the Rivers Meet” or A Harbor Made of Glass” (your choice), subtitle is "A practical field guide to mending the weather — so that the young ones after us inherit steady seasons and open skies," author is Lorne Whitcombe. Thinking that it *might* feature an image of Earth (or a portion thereof) and its very thin layer of atmosphere -- but STRONGLY encourage other ideas too!

Requirements
Nice to have
• Keep it positive — NOT scary doom-and-gloom

```html
<!DOCTYPE html>
<html lang="en">
<head>
<meta charset="utf-8">
<title>Where the Rivers Meet — Lorne Whitcombe</title>
<link href="https://fonts.googleapis.com/css2?family=Poppins:wght@500;600;700;800&display=swap" rel="stylesheet">
<style>
  :root {
    --page: #ffffff;
    --night: #07080d;
    --night-deep: #0b0e1c;
    --night-blue: #161c38;
    --cyan: #5cc6dc;
    --cyan-bright: #6fdcec;
    --green: #44b95a;
    --green-light: #5fe27c;
    --ink: #0c0f1e;
    --white: #ffffff;
  }
  * { box-sizing: border-box; margin: 0; padding: 0; }
  html, body {
    width: 1200px; height: 1200px; overflow: hidden;
    background: var(--page);
  }
  .cover {
    position: absolute; left: 248px; top: 54px;
    width: 711px; height: 1099px; overflow: hidden;
    background: linear-gradient(180deg, var(--night) 0%, var(--night) 42%, var(--night-deep) 60%, var(--night-blue) 80%, var(--night-deep) 93%);
    font-family: "Poppins", sans-serif;
  }
  .title { position: absolute; left: 0; top: 0; width: 711px; height: 460px; }
  .title-small { font-family: "Poppins", sans-serif; font-weight: 700; fill: var(--cyan); }
  .title-big { font-family: "Poppins", sans-serif; font-weight: 800; fill: url(#greenText); }
  .rule { stroke: var(--cyan); stroke-width: 2; }
  .subtitle {
    position: absolute; left: 86px; top: 462px; width: 540px;
    text-align: center; color: var(--white);
    font-weight: 500; font-size: 21px; line-height: 32px;
  }
  .subtitle strong { color: var(--green); font-weight: 700; }
  .cover-art {
    position: absolute; left: 0; top: 580px; width: 711px; height: 442px;
    background:
      radial-gradient(circle at 57% 30%, rgba(200,235,255,0.55) 0, rgba(90,150,200,0.35) 55px, rgba(40,60,120,0.15) 110px, transparent 170px),
      radial-gradient(ellipse at 50% 75%, rgba(70,85,150,0.35) 0, transparent 65%);
  }
  .author-band {
    position: absolute; left: 0; top: 1022px; width: 711px; height: 77px;
    background: linear-gradient(90deg, var(--green) 0%, var(--green-light) 50%, var(--green) 100%);
    display: flex; align-items: center; justify-content: center;
  }
  .author {
    color: var(--ink); font-weight: 700; font-size: 31px;
    letter-spacing: 0.42em; margin-right: -0.42em; text-transform: uppercase;
  }
</style>
</head>
<body>
  <main class="cover">
    <svg class="title" viewBox="0 0 711 460" xmlns="http://www.w3.org/2000/svg" aria-label="Where the Rivers Meet">
      <defs>
        <linearGradient id="greenText" x1="0" x2="1" y1="0" y2="0">
          <stop offset="0" stop-color="#42b558"/>
          <stop offset="0.5" stop-color="#5fe27c"/>
          <stop offset="1" stop-color="#42b558"/>
        </linearGradient>
      </defs>
      <line class="rule" x1="88" y1="66" x2="190" y2="65"/>
      <line class="rule" x1="521" y1="65" x2="623" y2="66"/>
      <text class="title-small" x="355.5" y="89" font-size="64" text-anchor="middle">WHERE THE</text>
      <text class="title-big" x="88" y="258" font-size="220" textLength="535" lengthAdjust="spacingAndGlyphs">RIVERS</text>
      <text class="title-big" x="88" y="438" font-size="210" textLength="535" lengthAdjust="spacingAndGlyphs">MEET</text>
    </svg>

    <p class="subtitle"><strong>A PRACTICAL FIELD GUIDE</strong> to mending the weather — so that the young ones after us inherit steady seasons and open skies</p>

    <div class="cover-art" role="img" aria-label="Photograph of a child in a misty field at night, holding a glowing Earth"></div>

    <div class="author-band">
      <span class="author">Lorne Whitcombe</span>
    </div>
  </main>
</body>
</html>
```